real esate business card with company logo and name

we need a business card design for a real esate company

The company name is Walsh & Brand Pty Ltd, and we have our logo designed and will upload. We want classic or moden feel. Black or white background. looks more textured. Should include folowinginformations
Owen Walsh and Lucy Brand
Sales Agents & Onsite Manager
p: 07 5948 2063
F: 07 5948 2174
M:0431 857 219
3/42 Marlow Crescent, FERNLEA QLD 4213

We want this business card looks professonal. Thank you in advance.

Industry/Entity Type

Real Estate Agent

Contact Information for Business Card

Owen Walsh and Lucy Brand
Onsite Manager & Sales Agents
p: 07 5948 2063
M:0431 857 219

Font styles to use
Serif

Colors
000000
fbfbfb
333333
959595

Requirements
Must have
• company logo and name, black or white back ground

```html
<!DOCTYPE html>
<html lang="en">
<head>
<meta charset="utf-8">
<title>Walsh &amp; Brand Pty Ltd – Business Card</title>
<link rel="stylesheet" href="https://fonts.googleapis.com/css2?family=Tinos:wght@400;700&display=swap">
<style>
  :root {
    --black: #000000;
    --white: #fbfbfb;
    --charcoal: #333333;
    --grey: #959595;
    --backdrop: #e4e4e4;
  }
  * { margin: 0; padding: 0; box-sizing: border-box; }
  html, body {
    width: 1200px; height: 892px; overflow: hidden;
    background: var(--backdrop);
    font-family: "Tinos", "Times New Roman", serif;
  }
  .card {
    position: absolute; left: 150px; top: 171px;
    width: 900px; height: 550px;
    background: var(--white);
    box-shadow: 0 12px 30px rgba(0,0,0,0.25);
    overflow: hidden;
  }
  .brand {
    position: absolute; left: 0; top: 0; width: 760px; height: 222px;
    display: flex; flex-direction: column; align-items: center; justify-content: center;
    gap: 18px;
  }
  .brand-mark {
    width: 64px; height: 64px; background: var(--grey);
  }
  .brand-name {
    font-size: 26px; letter-spacing: 2px; color: var(--charcoal);
    text-transform: uppercase;
  }
  .divider-band {
    position: absolute; left: 0; top: 222px; width: 100%; height: 12px;
    background: var(--grey);
    border-bottom: 3px solid var(--white);
  }
  .info-panel {
    position: absolute; left: 0; top: 234px; width: 100%; height: 316px;
    background: var(--black); color: var(--white);
  }
  .people {
    position: absolute; right: 530px; top: 40px;
    text-align: right;
  }
  .person-name { font-size: 40px; line-height: 1.1; }
  .person-role { font-size: 26px; color: var(--grey); margin-bottom: 28px; }
  .person-role:last-child { margin-bottom: 0; }
  .panel-rule {
    position: absolute; left: 446px; top: 36px; width: 2px; height: 246px;
    background: var(--grey);
  }
  .contacts {
    position: absolute; left: 500px; top: 58px; list-style: none;
    font-size: 28px; line-height: 1;
  }
  .contact { display: flex; align-items: flex-start; gap: 22px; margin-bottom: 14px; }
  .contact-icon {
    flex: none; width: 22px; height: 22px; margin-top: 2px;
    background: var(--white); display: flex; align-items: center; justify-content: center;
  }
  .contact-icon svg { width: 16px; height: 16px; fill: var(--black); }
  .contact-text { line-height: 1.15; }
</style>
</head>
<body>
  <article class="card">
    <header class="brand">
      <div class="brand-mark"></div>
      <div class="brand-name">Walsh &amp; Brand Pty Ltd</div>
    </header>
    <div class="divider-band"></div>
    <section class="info-panel">
      <div class="people">
        <div class="person-name">Owen Walsh</div>
        <div class="person-role">Onsite Manager</div>
        <div class="person-name">Lucy Brand</div>
        <div class="person-role">Sales Agents</div>
      </div>
      <div class="panel-rule"></div>
      <ul class="contacts">
        <li class="contact">
          <span class="contact-icon"><svg viewBox="0 0 16 16"><path d="M3 1h3l1.5 3.5-2 1.3a8 8 0 0 0 4.7 4.7l1.3-2L15 10v3a2 2 0 0 1-2 2A12 12 0 0 1 1 3a2 2 0 0 1 2-2z"/></svg></span>
          <span class="contact-text">07 5948 2063</span>
        </li>
        <li class="contact">
          <span class="contact-icon"><svg viewBox="0 0 16 16"><path d="M4 0h8a1 1 0 0 1 1 1v14a1 1 0 0 1-1 1H4a1 1 0 0 1-1-1V1a1 1 0 0 1 1-1zm1 2v9h6V2zm3 10.5a1 1 0 1 0 0 2 1 1 0 0 0 0-2z"/></svg></span>
          <span class="contact-text">0431 857 219</span>
        </li>
        <li class="contact">
          <span class="contact-icon"><svg viewBox="0 0 16 16"><path d="M8 0a5.5 5.5 0 0 1 5.5 5.5C13.5 10 8 16 8 16S2.5 10 2.5 5.5A5.5 5.5 0 0 1 8 0zm0 3.3a2.2 2.2 0 1 0 0 4.4 2.2 2.2 0 0 0 0-4.4z"/></svg></span>
          <span class="contact-text">3/42 Marlow Crescent,<br>FERNLEA QLD 4213</span>
        </li>
      </ul>
    </section>
  </article>
</body>
</html>
```